Tech business card design

We need an amazing business card design for our new business 'Pexla' a marketing tech startup based in Sydney, Australia. We provide an online marketplace for businesses to search and buy advertising media, connect with service providers and learn more about marketing. We wish to communicate 'cool tech', reliability and professionalism and design based around our logo.

Target Market(s)

Business Owners

Contact Information for Business Card

Name
Position
Email Address
Website
Phone Number

Font styles to use
Other font styles liked:
• Avenir & Avenir Next

Colors

Designer to choose colors to be used in the design.

```html
<!DOCTYPE html>
<html lang="en">
<head>
<meta charset="utf-8">
<title>Pexla Business Card</title>
<link rel="stylesheet" href="https://fonts.googleapis.com/css2?family=Source+Sans+3:wght@400;900&display=swap">
<style>
  :root {
    --page-bg: #e2dfdf;
    --card-bg: #ffffff;
    --card-edge: #a9a9ad;
    --navy: #1b1c40;
    --navy-band: #262a4b;
    --mist: #dadae4;
    --white: #ffffff;
  }
  * { margin: 0; padding: 0; box-sizing: border-box; }
  html, body { width: 975px; height: 1200px; overflow: hidden; }
  body {
    background: var(--page-bg);
    font-family: "Source Sans 3", "Avenir Next", Avenir, sans-serif;
    position: relative;
  }
  .card {
    position: absolute;
    left: 58px;
    width: 859px;
    height: 492px;
    background: var(--card-bg);
    border: 1px solid var(--card-edge);
    border-radius: 42px;
    overflow: hidden;
  }
  .card--front { top: 79px; }
  .card--back { top: 644px; }
  .card__shapes { position: absolute; inset: 0; width: 100%; height: 100%; }
  .wordmark {
    position: absolute;
    left: 0;
    width: 100%;
    text-align: center;
    font-weight: 900;
    font-size: 168px;
    line-height: 1;
    letter-spacing: -2px;
    color: var(--navy);
  }
  .card--front .wordmark { top: 52px; }
  .card--back .wordmark { top: 125px; }
  .contact {
    position: absolute;
    left: 0;
    width: 100%;
    text-align: center;
    color: var(--navy);
    font-size: 22px;
    font-weight: 400;
  }
  .contact--address { top: 393px; padding-right: 40px; }
  .contact--lines {
    top: 432px;
    display: flex;
    justify-content: center;
    gap: 14px;
    align-items: center;
  }
  .contact__item { display: inline-flex; align-items: center; gap: 5px; }
  .contact__icon { width: 20px; height: 20px; }
  .back-url {
    position: absolute;
    top: 406px;
    left: 0;
    width: 100%;
    text-align: center;
    color: var(--white);
    font-size: 26px;
    letter-spacing: 3px;
  }
</style>
</head>
<body>

<section class="card card--front">
  <svg class="card__shapes" viewBox="0 0 1050 607" preserveAspectRatio="none" aria-hidden="true">
    <path d="M0 494 Q525 300 1050 494 L1050 607 L0 607 Z" fill="var(--mist)"/>
    <path d="M30 459 Q520 270 1050 490" fill="none" stroke="var(--navy)" stroke-width="5"/>
  </svg>
  <div class="wordmark">pexla</div>
  <p class="contact contact--address">Street name City Name Zipcode,012345</p>
  <div class="contact contact--lines">
    <span class="contact__item">
      <svg class="contact__icon" viewBox="0 0 20 20" aria-hidden="true">
        <circle cx="10" cy="10" r="8.5" fill="none" stroke="var(--navy)" stroke-width="1.6"/>
        <path d="M6.5 5.5 l2 -0.5 l1 2.6 l-1.3 1 q1 2 2.6 2.8 l1 -1.3 l2.6 1 l-0.5 2 q-4 0.3 -6.6 -3 q-1.8 -2.4 -0.8 -4.6z" fill="var(--navy)"/>
      </svg>012-345-6789
    </span>
    <span class="contact__item">
      <svg class="contact__icon" viewBox="0 0 20 20" aria-hidden="true">
        <rect x="1.5" y="4.5" width="17" height="11" fill="var(--navy)"/>
        <path d="M1.5 4.5 L10 11 L18.5 4.5 M1.5 15.5 L7.5 9.5 M18.5 15.5 L12.5 9.5" fill="none" stroke="var(--mist)" stroke-width="1.3"/>
      </svg>info@pexla.com
    </span>
    <span class="contact__item">
      <svg class="contact__icon" viewBox="0 0 20 20" aria-hidden="true">
        <g fill="none" stroke="var(--navy)" stroke-width="1.4">
          <circle cx="10" cy="10" r="8.5"/>
          <ellipse cx="10" cy="10" rx="3.8" ry="8.5"/>
          <path d="M1.5 10 H18.5 M3 5.5 H17 M3 14.5 H17 M10 1.5 V18.5"/>
        </g>
      </svg>www.pexla.com
    </span>
  </div>
</section>

<section class="card card--back">
  <svg class="card__shapes" viewBox="0 0 1050 607" preserveAspectRatio="none" aria-hidden="true">
    <path d="M169 463 Q540 370 919 468 Q540 400 169 463 Z" fill="var(--mist)"/>
    <path d="M0 513 Q520 360 1050 503 L1050 607 L0 607 Z" fill="var(--navy-band)"/>
  </svg>
  <div class="wordmark">pexla</div>
  <p class="back-url">www.pexla.com</p>
</section>

</body>
</html>
```